Business Card Design for company

We want new business cards. We'd like something different-- yet still highly professional. Our tagline is Providing leadership, delivering success. Stock photos are ok, as long as they are relevant and look upscale.

Target Market(s)

Architecture/Business Management Consulting/Engineering Consulting

Contact Information for Business Card

dark gray background with pops of blue might be good, but you tell me. You're the designers. Rounded corners might be nice, but again, you tell me.

Font styles to use
Serif
Sans Serif

Colors
3276b5
5c5c5c
9d9d9d
fbfbfb

Requirements
Nice to have
• Something different, but still very professional.

```html
<!DOCTYPE html>
<html lang="en">
<head>
<meta charset="utf-8">
<title>Norvik International – Business Card</title>
<link rel="stylesheet" href="https://fonts.googleapis.com/css2?family=Open+Sans:wght@400;600&display=swap">
<style>
  :root {
    --brand-blue: #3276b5;
    --brand-gray: #5c5c5c;
    --soft-gray: #9d9d9d;
    --paper: #fbfbfb;
    --ink: #2e2e2e;
    --backdrop: #e4e4e4;
  }
  html, body {
    margin: 0;
    padding: 0;
    width: 1200px;
    height: 1023px;
    overflow: hidden;
    background: var(--backdrop);
    font-family: "Open Sans", sans-serif;
  }
  .business-card {
    position: absolute;
    left: 100px;
    top: 226px;
    width: 1000px;
    height: 571px;
    background: var(--paper);
    border-radius: 4px;
    box-shadow: 0 10px 30px rgba(0,0,0,0.18);
    overflow: hidden;
  }
  .card-swoosh {
    position: absolute;
    inset: 0;
    width: 100%;
    height: 100%;
  }
  .brand-name {
    position: absolute;
    right: 110px;
    top: 70px;
    display: flex;
    align-items: center;
    gap: 22px;
    color: var(--brand-blue);
    font-weight: 600;
  }
  .brand-mark {
    width: 26px;
    height: 26px;
    background: var(--brand-blue);
    flex: none;
  }
  .brand-words {
    line-height: 1;
    text-align: right;
  }
  .brand-words .primary {
    display: block;
    font-size: 96px;
    letter-spacing: 4px;
  }
  .brand-words .secondary {
    display: block;
    font-size: 34px;
    letter-spacing: 6px;
    margin-top: 10px;
  }
  .person {
    position: absolute;
    left: 70px;
    top: 228px;
  }
  .person-name {
    margin: 0;
    color: var(--brand-blue);
    font-size: 32px;
    font-weight: 400;
    line-height: 1.1;
  }
  .person-title {
    margin: 2px 0 0;
    color: var(--ink);
    font-size: 22px;
  }
  .contact-list {
    position: absolute;
    left: 70px;
    top: 336px;
    margin: 0;
    padding: 0;
    list-style: none;
    color: var(--ink);
    font-size: 22px;
    line-height: 34px;
  }
  .contact-list li {
    display: flex;
    align-items: flex-start;
    gap: 14px;
  }
  .contact-icon {
    flex: none;
    width: 22px;
    height: 22px;
    margin-top: 6px;
  }
</style>
</head>
<body>
  <section class="business-card">
    <svg class="card-swoosh" viewBox="0 0 1000 571" preserveAspectRatio="none" aria-hidden="true">
      <path d="M400 571 C 610 520, 790 420, 1000 285 L1000 571 Z" fill="var(--brand-gray)"/>
      <path d="M470 571 C 660 525, 815 432, 1000 312 L1000 571 Z" fill="var(--paper)"/>
      <path d="M490 571 C 675 528, 825 440, 1000 324 L1000 571 Z" fill="var(--brand-blue)"/>
    </svg>

    <div class="brand-name">
      <span class="brand-mark"></span>
      <span class="brand-words">
        <span class="primary">NORVIK</span>
        <span class="secondary">INTERNATIONAL</span>
      </span>
    </div>

    <div class="person">
      <h1 class="person-name">Daniel Moreau</h1>
      <p class="person-title">Owner</p>
    </div>

    <ul class="contact-list">
      <li>
        <svg class="contact-icon" viewBox="0 0 22 22"><rect width="22" height="22" rx="3" fill="var(--brand-blue)"/><path d="M7 5 L9 5 L10 8 L8.5 9.2 C9.3 11 10.8 12.6 12.8 13.5 L14 12 L17 13 L17 15 C17 16 16 17 15 17 C9.5 16.6 5.4 12.5 5 7 C5 6 6 5 7 5 Z" fill="#fff"/></svg>
        <span>+0000-0000-0000</span>
      </li>
      <li>
        <svg class="contact-icon" viewBox="0 0 22 22"><rect width="22" height="22" rx="3" fill="var(--brand-blue)"/><rect x="5" y="7" width="12" height="9" fill="none" stroke="#fff" stroke-width="1.6"/><path d="M5 7 L11 12 L17 7" fill="none" stroke="#fff" stroke-width="1.6"/></svg>
        <span>info@yourdomain.com</span>
      </li>
      <li>
        <svg class="contact-icon" viewBox="0 0 22 22"><rect width="22" height="22" rx="3" fill="var(--brand-blue)"/><circle cx="11" cy="11" r="6" fill="none" stroke="#fff" stroke-width="1.5"/><ellipse cx="11" cy="11" rx="2.6" ry="6" fill="none" stroke="#fff" stroke-width="1.3"/><path d="M5 11 H17" stroke="#fff" stroke-width="1.3"/></svg>
        <span>www.yourdomain.com</span>
      </li>
      <li>
        <svg class="contact-icon" viewBox="0 0 22 22"><rect width="22" height="22" rx="3" fill="var(--brand-blue)"/><path d="M11 4.5 C8.2 4.5 6.2 6.6 6.2 9.2 C6.2 12.6 11 17.5 11 17.5 C11 17.5 15.8 12.6 15.8 9.2 C15.8 6.6 13.8 4.5 11 4.5 Z" fill="#fff"/><circle cx="11" cy="9.2" r="1.8" fill="var(--brand-blue)"/></svg>
        <span>Suite 210, 48 Harbour Lane,<br>Bristol</span>
      </li>
    </ul>
  </section>
</body>
</html>
```